Brochure condensed from the PDF marketing

An organised brochure with 4 x banner heading for the various portfolios,
Condensed and made into a 4 page booklet or neat and tidy brochure display that can be easily emailed to prospective customers. The brochure should be neat and professional similar content to the website to send the 4 x Portfolios to the various Industry Categories, thank you

** Ive just uploaded a couple of extra photos for the ' Our Services ' area on the Brochure, pls add the ice cream one for the ' Parfait Cleaning and Sanitisation Services, and on the ' Our Services' category for the High pressure Gurney and Playground Cleaning pls add a fun photo for example the one I sent with people having fun on the playground equipment, **

HI KT Designer The brochure design is for my facebook title page /Users/user/Desktop/Screenshot 2020-05-05 at 9.22.39 PM.png Under Brightwell Facebook Design (Contest) DO you have a direct email, its very difficult to keep posing images and updates here Thank you Imogen @ Brightwell.

Target Market(s)

Cleaning Services

Font styles to use
Serif

Requirements
Must have
• Look professional and neat and tidy brochure booklet for marketing on email to prospective customers.

```html
<!DOCTYPE html>
<html lang="en">
<head>
<meta charset="utf-8">
<title>Brightwell Brochure</title>
<link rel="stylesheet" href="https://fonts.googleapis.com/css2?family=Noto+Serif:wght@400;700&family=Roboto+Condensed:wght@300;400;700&display=swap">
<style>
:root{
  --orange:#f1561d;
  --orange-light:#f77a3c;
  --navy:#123c7c;
  --navy-deep:#0d3270;
  --paper:#f4f4f6;
  --backdrop:#d8d8da;
  --ink:#1d3f7a;
  --serif:'Noto Serif',Georgia,serif;
  --sans:'Roboto Condensed','Arial Narrow',sans-serif;
}
*{box-sizing:border-box;margin:0;padding:0}
html,body{width:1200px;height:2769px;overflow:hidden}
body{background:var(--backdrop);position:relative;font-family:var(--sans);color:var(--ink)}
.page{position:absolute;width:522px;height:737px;background:var(--paper);overflow:hidden;box-shadow:0 4px 14px rgba(0,0,0,.22)}
.page--hero{left:327px;top:178px;transform:scale(1.08);transform-origin:0 0}
.page--cover{left:61px;top:1195px}
.page--about{left:610px;top:1195px}
.page--services{left:61px;top:1960px}
.page--back{left:612px;top:1960px;background:var(--navy)}

/* brand name */
.brand{display:flex;align-items:center;gap:12px;font-family:var(--serif);color:var(--orange)}
.brand__dot{width:40px;height:40px;border-radius:50%;background:var(--navy);flex:none}
.brand__name{font-size:46px;font-weight:400;line-height:1}

/* cover */
.cover__brand{position:absolute;top:36px;left:0;right:0;justify-content:center}
.cover__rule{position:absolute;top:127px;left:52px;right:0;height:8px;background:var(--orange)}
.cover__grid{position:absolute;top:135px;left:0;width:522px;height:415px}
.cover__grid svg{display:block}
.tag{position:absolute;font-family:var(--sans);color:#fff;line-height:1.05;font-size:16px;font-weight:300;text-transform:uppercase}
.tag b{display:block;font-weight:700;font-size:17px}
.tag--l{left:22px}
.tag--r{right:22px;text-align:right}
.cover__welcome{position:absolute;top:582px;left:0;right:0;text-align:center;font-family:var(--serif)}
.cover__lead{font-size:42px;color:var(--navy);line-height:1}
.cover__title{font-size:56px;font-weight:700;color:var(--orange);line-height:1.05;letter-spacing:1px}
.cover__url{font-size:18px;color:var(--navy);margin-top:6px}

/* about */
.about__photo{position:absolute;left:0;top:0;width:280px;height:270px}
.about__intro{position:absolute;left:272px;top:30px;width:228px;font-size:10px;line-height:1.3}
.about__intro h2{font-family:var(--serif);font-weight:700;font-size:19px;line-height:1;color:var(--navy);margin-bottom:12px;text-transform:uppercase}
.about__intro h2 span{color:var(--orange)}
.about__intro p{margin-bottom:10px;text-align:justify}
.pillars{position:absolute;left:25px;top:280px;display:flex;gap:5px}
.pillar{width:155px;height:278px;background:var(--navy);color:#fff;text-align:center}
.pillar__icon{height:97px;background:var(--orange);display:flex;align-items:center;justify-content:center}
.pillar h3{font-family:var(--serif);font-weight:700;font-size:13px;margin:12px 0 8px}
.pillar p{font-size:9.6px;line-height:1.25;padding:0 14px}
.values{position:absolute;left:25px;top:580px;width:475px}
.values h2{font-family:var(--serif);font-weight:700;font-size:18px;color:var(--navy);margin-bottom:6px}
.values h2 span,.services h2 span,.staff h2 span,.safety h2 span{color:var(--orange)}
.values p{font-size:8.4px;line-height:1.65;color:var(--navy)}
.values b{font-weight:700}

/* footer */
.footer{position:absolute;left:20px;right:0;bottom:20px;display:flex;align-items:center;gap:8px}
.footer .brand{gap:6px}
.footer .brand__dot{width:18px;height:18px}
.footer .brand__name{font-size:20px}
.footer__line{flex:1;height:1px;background:var(--navy)}
.footer__num{width:22px;height:22px;background:var(--orange);color:#fff;font-family:var(--serif);font-weight:700;font-size:14px;display:flex;align-items:center;justify-content:center;margin-right:10px}

/* services */
.services{position:absolute;left:0;top:22px;width:522px;text-align:center}
.services h2,.safety h2,.staff h2{font-family:var(--serif);font-weight:700;font-size:18px;color:var(--navy)}
.services__list{display:flex;justify-content:center;gap:20px;margin-top:18px}
.service{width:100px}
.service__photo{width:100px;height:100px;border-radius:50%;border:4px solid #fff;box-shadow:0 1px 4px rgba(0,0,0,.25);display:block}
.service p{font-family:var(--serif);font-size:11.5px;line-height:1.25;color:var(--navy);margin-top:10px}
.safety{position:absolute;left:0;top:260px;width:522px;height:265px;background:var(--navy);color:#fff;text-align:center;padding:18px 28px 0}
.safety h2{color:#fff;margin-bottom:12px}
.safety p{font-size:9.6px;line-height:1.3;margin-bottom:12px;text-align:justify;text-align-last:center}
.staff{position:absolute;left:25px;top:538px;width:475px}
.staff h2{margin-bottom:6px}
.staff p{font-size:8.6px;line-height:1.35;margin-bottom:10px;text-align:justify}

/* back */
.back__brand{position:absolute;top:78px;left:0;right:0;justify-content:center}
.back__brand .brand__dot{background:#fff}
.back__contact{position:absolute;top:160px;left:0;right:0;text-align:center;color:#fff;font-family:var(--serif);font-size:14px;line-height:1.2}
</style>
</head>
<body>

<!-- hero cover -->
<section class="page page--hero cover" aria-label="Brochure cover">
  <div class="brand cover__brand"><span class="brand__dot"></span><span class="brand__name">Brightwell</span></div>
  <div class="cover__rule"></div>
  <div class="cover__grid">
    <svg width="522" height="415" viewBox="0 0 522 415">
      <defs>
        <linearGradient id="hb1" x1="0" x2="1"><stop offset="0" stop-color="#e9480f"/><stop offset="1" stop-color="#f66a2a"/></linearGradient>
        <linearGradient id="hw1" x1="0" x2="1"><stop offset="0" stop-color="#c88a4e"/><stop offset="1" stop-color="#9a9590"/></linearGradient>
        <linearGradient id="hp1" x1="0" x2="1" y1="0" y2="1"><stop offset="0" stop-color="#8dbd5a"/><stop offset="1" stop-color="#5b8a3b"/></linearGradient>
        <linearGradient id="hs1" x1="0" x2="1" y1="0" y2="1"><stop offset="0" stop-color="#3f8fb0"/><stop offset="1" stop-color="#b9d0dc"/></linearGradient>
        <linearGradient id="hj1" x1="0" x2="1" y1="0" y2="1"><stop offset="0" stop-color="#6d6f66"/><stop offset="1" stop-color="#a55f4c"/></linearGradient>
      </defs>
      <polygon points="0,0 312,0 256,207 0,207" fill="url(#hw1)" role="img" aria-label="Photo: wooden chopping board washed under a kitchen tap"/>
      <polygon points="318,0 522,0 522,207 262,207" fill="url(#hp1)" role="img" aria-label="Photo: children carrying a recycling tub in a park"/>
      <polygon points="0,210 255,210 205,415 0,415" fill="url(#hs1)" role="img" aria-label="Photo: stainless steel commercial kitchen equipment"/>
      <polygon points="261,210 522,210 522,415 211,415" fill="url(#hj1)" role="img" aria-label="Photo: worker pressure washing paving"/>
      <polygon points="0,155 270,155 256,207 0,207" fill="url(#hb1)"/>
      <polygon points="276,155 522,155 522,207 262,207" fill="url(#hb1)" opacity=".92"/>
      <polygon points="0,362 218,362 205,415 0,415" fill="url(#hb1)"/>
      <polygon points="224,362 522,362 522,415 211,415" fill="url(#hb1)" opacity=".92"/>
    </svg>
    <div class="tag tag--l" style="top:161px">Food service equipment<b>Cleaning</b></div>
    <div class="tag tag--r" style="top:161px">Playground<b>Cleaning</b></div>
    <div class="tag tag--l" style="top:368px">Commercial restaurant<b>Cleaning</b></div>
    <div class="tag tag--r" style="top:368px">High pressure water<b>Cleaning</b></div>
  </div>
  <div class="cover__welcome">
    <div class="cover__lead">Welcome to</div>
    <div class="cover__title">BRIGHTWELL</div>
    <div class="cover__url">www.brightwellclean.com.au</div>
  </div>
</section>

<!-- cover page -->
<section class="page page--cover cover" aria-label="Brochure cover">
  <div class="brand cover__brand"><span class="brand__dot"></span><span class="brand__name">Brightwell</span></div>
  <div class="cover__rule"></div>
  <div class="cover__grid">
    <svg width="522" height="415" viewBox="0 0 522 415">
      <polygon points="0,0 312,0 256,207 0,207" fill="url(#hw1)" role="img" aria-label="Photo: wooden chopping board washed under a kitchen tap"/>
      <polygon points="318,0 522,0 522,207 262,207" fill="url(#hp1)" role="img" aria-label="Photo: children carrying a recycling tub in a park"/>
      <polygon points="0,210 255,210 205,415 0,415" fill="url(#hs1)" role="img" aria-label="Photo: stainless steel commercial kitchen equipment"/>
      <polygon points="261,210 522,210 522,415 211,415" fill="url(#hj1)" role="img" aria-label="Photo: worker pressure washing paving"/>
      <polygon points="0,155 270,155 256,207 0,207" fill="url(#hb1)"/>
      <polygon points="276,155 522,155 522,207 262,207" fill="url(#hb1)" opacity=".92"/>
      <polygon points="0,362 218,362 205,415 0,415" fill="url(#hb1)"/>
      <polygon points="224,362 522,362 522,415 211,415" fill="url(#hb1)" opacity=".92"/>
    </svg>
    <div class="tag tag--l" style="top:161px">Food service equipment<b>Cleaning</b></div>
    <div class="tag tag--r" style="top:161px">Playground<b>Cleaning</b></div>
    <div class="tag tag--l" style="top:368px">Commercial restaurant<b>Cleaning</b></div>
    <div class="tag tag--r" style="top:368px">High pressure water<b>Cleaning</b></div>
  </div>
  <div class="cover__welcome">
    <div class="cover__lead">Welcome to</div>
    <div class="cover__title">BRIGHTWELL</div>
    <div class="cover__url">www.brightwellclean.com.au</div>
  </div>
</section>

<!-- page 1 -->
<section class="page page--about" aria-label="Working with Brightwell">
  <svg class="about__photo" viewBox="0 0 280 270" role="img" aria-label="Photo collage: carpet steam cleaning with a cleaner in blue overshoes">
    <defs><linearGradient id="ab" x1="0" x2="1" y1="0" y2="1"><stop offset="0" stop-color="#8c8f94"/><stop offset=".6" stop-color="#b9bcc2"/><stop offset="1" stop-color="#e6e7ea"/></linearGradient></defs>
    <rect width="280" height="270" fill="url(#ab)"/>
  </svg>
  <div class="about__intro">
    <h2>Working<br>with <span>Brightwell</span></h2>
    <p>We are Brightwell, a leading, Australian owned, cleaning services company.</p>
    <p>When you work with Brightwell it is easy to do business with us.</p>
    <p>Our people are professional, reliable and service oriented. In every interaction you have; on site, receiving help from our service support staff, or rolling-out new cleaning sites, you will see and feel the benefits of using Brightwell. The pride we take in our work and a prevailing focus on employees, customers and partners, delivers a consistent and superior ongoing service.</p>
  </div>
  <div class="pillars">
    <div class="pillar">
      <div class="pillar__icon"><svg width="44" height="44" viewBox="0 0 44 44" aria-hidden="true"><circle cx="22" cy="16" r="9" fill="none" stroke="#fff" stroke-width="3"/><rect x="10" y="30" width="24" height="8" fill="#fff"/></svg></div>
      <h3>OUR PURPOSE</h3>
      <p>To support and extend the life of equipment, maximize product yield and achieve high quality hygiene standards for our food and equipment service clients. We deliver this by ensuring every person in our service chain delivers their work focusing on high quality and reliable cleaning standards.</p>
    </div>
    <div class="pillar">
      <div class="pillar__icon"><svg width="60" height="60" viewBox="0 0 60 60" aria-hidden="true"><polygon points="30,2 34,26 58,30 34,34 30,58 26,34 2,30 26,26" fill="#fff"/></svg></div>
      <h3>OUR VISION</h3>
      <p>A sustainable food service and equipment cleaning company that creates value for customers, supports its employees in work and life and gives back to the community – now and for generations to come.</p>
    </div>
    <div class="pillar">
      <div class="pillar__icon"><svg width="60" height="60" viewBox="0 0 60 60" aria-hidden="true"><circle cx="30" cy="30" r="26" fill="none" stroke="#fff" stroke-width="3"/><polygon points="42,18 33,33 18,42 27,27" fill="#fff"/></svg></div>
      <h3>OUR STRATEGY</h3>
      <p>To differentiate ourselves through a prevailing focus on customer service, in everything we do and every interaction we have. We treat our people as skilled cleaning professionals who are the foundation of our company's sustainability.</p>
    </div>
  </div>
  <div class="values">
    <h2>WE <span>VALUE</span></h2>
    <p><b>Safety and the Environment</b> – We are committed to providing a safe and healthy working environment;<br>
    <b>Professionalism/Integrity</b> – We are committed to doing what we say we are going to do;<br>
    <b>Sustainability</b> – Achieving results that are mutually beneficial for our employees, our customers, our partners and the company;<br>
    <b>Positive Working Relationships</b> – Having relationships that focus on shared goals and creation of value for all parties;<br>
    <b>Respect for Each Other</b> – The embracing of diversity, enriched by openness, sharing, trust, teamwork and involvement.</p>
  </div>
  <div class="footer"><div class="brand"><span class="brand__dot"></span><span class="brand__name">Brightwell</span></div><span class="footer__line"></span><span class="footer__num">1</span></div>
</section>

<!-- page 2 -->
<section class="page page--services" aria-label="Our services">
  <div class="services">
    <h2>OUR <span>SERVICES</span></h2>
    <div class="services__list">
      <div class="service"><svg class="service__photo" viewBox="0 0 100 100" role="img" aria-label="Photo: chopping board being washed"><rect width="100" height="100" fill="#c98a55"/></svg><p>Equipment Cleaning &amp; Sanitisation Services</p></div>
      <div class="service"><svg class="service__photo" viewBox="0 0 100 100" role="img" aria-label="Photo: window cleaners on a glass building"><rect width="100" height="100" fill="#4d86b4"/></svg><p>General Cleaning &amp; Property Facilities Management</p></div>
      <div class="service"><svg class="service__photo" viewBox="0 0 100 100" role="img" aria-label="Photo: pressure washing paving"><rect width="100" height="100" fill="#8a6a5e"/></svg><p>High Pressure gurney &amp; play ground equipment Cleaning</p></div>
      <div class="service"><svg class="service__photo" viewBox="0 0 100 100" role="img" aria-label="Photo: team hands joined together"><rect width="100" height="100" fill="#b88f86"/></svg><p>Projects and Recruiting Services Work with us</p></div>
    </div>
  </div>
  <div class="safety">
    <h2>SAFETY &amp; <span>COMPLIANCE</span></h2>
    <p>Brightwell values safety and environment. We have an overriding commitment to health, safety and environmental responsibility.</p>
    <p>Each member of our company community undergoes a yearly on-line safety refresher course, and performs a routine reflection safety check and risk assessment at each clients site on attending work each day. We have safety work method statements in place and work on ensuring our people work safely on site through practical application of safety steps, safety shoes and appropriate personal protection equipment (PPE) work gear.</p>
    <p>Brightwell is covered with $20,000,000 General and Product Liability coverage through Harbourline Insurance LTD and has work cover in place for all our employees across Sydney, Brisbane, Melbourne, Newcastle and Adelaide.</p>
    <p>Brightwell employees always aspire to work safely whilst on client sites.</p>
  </div>
  <div class="staff">
    <h2>OUR <span>STAFF</span></h2>
    <p>We are proud of our team. The majority of staff has been with the company for many years. As a result, the understanding of our clients and our bench strength of cleaning professionals is extremely strong.</p>
    <p>Our people are carefully selected from qualified trades backgrounds, or, equivalent on the job experience. They are career focused cleaning and maintenance professionals with backgrounds that include refrigeration and automobile mechanics, fitters and turners, and machinists.</p>
    <p>Service Technicians are provided ongoing training and development so they are always prepared for the rigors of delivering a disciplined and reliable service, including an extensive induction and buddy training system for new team members.</p>
  </div>
  <div class="footer"><div class="brand"><span class="brand__dot"></span><span class="brand__name">Brightwell</span></div><span class="footer__line"></span><span class="footer__num">2</span></div>
</section>

<!-- back page -->
<section class="page page--back" aria-label="Contact details">
  <div class="brand back__brand"><span class="brand__dot"></span><span class="brand__name">Brightwell</span></div>
  <div class="back__contact">
    Sydney | Brisbane | Melbourne | Adelaide<br>
    Australia ABN 51 824 000 317<br>
    Landline: 1300 555 018<br>
    Mobile: 0400 555 074<br>
    Email: service@brightwellclean.com.au<br>
    www.brightwellclean.com.au
  </div>
</section>

</body>
</html>
```